Moravel Aesthetic Doctor

I require an elegant, luxurious looking business card for my aesthetic business. I am a doctor and that will set me aside from competitors. I am planning to provide home and spa based treatments to clients with high expectations. I have attached my logo.

```html
<!DOCTYPE html>
<html lang="en">
<head>
<meta charset="utf-8">
<title>Moravel Aesthetic Doctor – Business Card</title>
<link rel="stylesheet" href="https://fonts.googleapis.com/css2?family=Arimo:wght@400;700&display=swap">
<style>
  :root {
    --backdrop: #b9b9bb;
    --card-grey: #a6a7aa;
    --card-white: #ffffff;
    --ink-grey: #8b8c90;
    --ink-light: #ffffff;
    --accent-blue: #5bb9e6;
    --accent-blue-deep: #2f8fd0;
    --ring-grey: #9a9b9e;
    --swirl: #eef0f3;
  }
  * { box-sizing: border-box; margin: 0; padding: 0; }
  html, body { width: 1200px; height: 900px; overflow: hidden; }
  body {
    background: var(--backdrop);
    font-family: "Arimo", Arial, sans-serif;
    display: flex;
    flex-direction: column;
    align-items: center;
    justify-content: center;
    gap: 48px;
  }
  .card {
    position: relative;
    width: 620px;
    height: 354px;
    border-radius: 26px;
    overflow: hidden;
    box-shadow: 0 6px 14px rgba(0,0,0,0.25);
  }

  /* Back of card */
  .card--back {
    background: var(--card-grey);
    color: var(--ink-light);
    display: flex;
    flex-direction: column;
    align-items: center;
    justify-content: center;
    text-align: center;
  }
  .lockup {
    display: flex;
    align-items: center;
    gap: 18px;
  }
  .lockup__mark {
    width: 78px;
    height: 78px;
    border-radius: 50%;
    border: 3px solid currentColor;
    flex: none;
  }
  .lockup__name {
    font-weight: 400;
    font-size: 30px;
    letter-spacing: 3px;
    text-transform: uppercase;
    line-height: 1.15;
    text-align: left;
  }
  .card--back .lockup { color: var(--ink-light); }
  .tagline {
    margin-top: 26px;
    font-size: 15px;
    letter-spacing: 1.5px;
    text-transform: uppercase;
  }
  .services {
    margin-top: 18px;
    list-style: none;
    font-size: 15px;
    line-height: 1.45;
  }
  .services .dot { margin: 0 8px; }

  /* Front of card */
  .card--front {
    background: var(--card-white);
    padding: 38px 44px;
  }
  .swirl {
    position: absolute;
    inset: 0;
    background:
      radial-gradient(ellipse 70% 90% at 75% 20%, var(--swirl) 0%, rgba(238,240,243,0) 70%),
      radial-gradient(ellipse 50% 70% at 40% 90%, #f3f4f6 0%, rgba(243,244,246,0) 70%);
  }
  .card--front .lockup { position: relative; color: var(--ink-grey); }
  .card--front .lockup__mark { border-color: var(--ring-grey); }
  .card--front .lockup__name { color: var(--ink-grey); font-size: 26px; }
  .holder {
    position: relative;
    margin-top: 46px;
  }
  .holder__name {
    font-weight: 700;
    font-size: 26px;
    color: var(--ink-grey);
  }
  .holder__post {
    font-weight: 400;
    font-size: 13px;
    color: var(--accent-blue);
    margin-left: 6px;
  }
  .holder__cred {
    font-size: 16px;
    color: var(--accent-blue);
    margin-top: 4px;
  }
  .contacts {
    position: relative;
    list-style: none;
    margin-top: 22px;
    font-size: 16px;
    color: var(--ink-grey);
  }
  .contacts li {
    display: flex;
    align-items: center;
    gap: 12px;
    height: 24px;
  }
  .contacts svg { width: 18px; height: 18px; flex: none; }
  .social {
    position: absolute;
    top: 40px;
    right: 40px;
    display: flex;
    gap: 6px;
  }
  .social span {
    width: 24px;
    height: 24px;
    border-radius: 50%;
    display: block;
  }
  .social .social--one { background: #3b5ba8; }
  .social .social--two { background: #d8386a; }
</style>
</head>
<body>

  <section class="card card--back">
    <div class="lockup">
      <span class="lockup__mark"></span>
      <span class="lockup__name">Moravel<br>Aesthetic Doctor</span>
    </div>
    <p class="tagline">Home and Spa Based Treatments</p>
    <ul class="services">
      <li>Dermal injectables<span class="dot">•</span>Plasma facials<span class="dot">•</span>Microneedling</li>
      <li>Skin boosters<span class="dot">•</span>Excessive sweating</li>
      <li>Home and Spa Based Treatments</li>
    </ul>
  </section>

  <section class="card card--front">
    <div class="swirl" role="img" aria-label="Faint flowing hair-strand decoration in soft grey"></div>

    <div class="lockup">
      <span class="lockup__mark"></span>
      <span class="lockup__name">Moravel<br>Aesthetic Doctor</span>
    </div>

    <div class="social" aria-label="Social media">
      <span class="social--one"></span>
      <span class="social--two"></span>
    </div>

    <div class="holder">
      <p><span class="holder__name">Dr Elin Varga</span><span class="holder__post">MRCPCH MD</span></p>
      <p class="holder__cred">Australasian Diploma of Aesthetic Medicine</p>
    </div>

    <ul class="contacts">
      <li>
        <svg viewBox="0 0 24 24" aria-hidden="true"><path fill="var(--accent-blue)" d="M6.6 10.8a15.1 15.1 0 0 0 6.6 6.6l2.2-2.2c.3-.3.7-.4 1-.2 1.1.4 2.3.6 3.6.6.6 0 1 .4 1 1V20c0 .6-.4 1-1 1A17 17 0 0 1 3 4c0-.6.4-1 1-1h3.5c.6 0 1 .4 1 1 0 1.3.2 2.5.6 3.6.1.3 0 .7-.2 1z"/></svg>
        0800 555 014
      </li>
      <li>
        <svg viewBox="0 0 24 24" aria-hidden="true"><rect x="2" y="5" width="20" height="14" rx="1.5" fill="var(--accent-blue)"/><path d="M3 6l9 7 9-7" fill="none" stroke="#fff" stroke-width="1.6"/></svg>
        elin@moravel.co.nz
      </li>
      <li>
        <svg viewBox="0 0 24 24" aria-hidden="true"><g fill="none" stroke="var(--accent-blue)" stroke-width="1.8"><circle cx="12" cy="12" r="9.5"/><ellipse cx="12" cy="12" rx="4" ry="9.5"/><path d="M2.5 12h19M4 7h16M4 17h16"/></g></svg>
        www.moravel.co.nz
      </li>
    </ul>
  </section>

</body>
</html>
```